Inspirational Quotes Poster Set

Brookloft is a stylish coworking space, which has a design-oriented vintage look from the 60's with an industrial touch (www.brookloft-example.com) Brookloft Quote Poster Set of 16 posters. The poster should be typo oriented and rather simple. Reflecting a bit the clean billboard design from the sixties. Minimal / simple graphical elements

Target Market(s)

Startups and Entrepreneurs

Industry/Entity Type

Startup

Font styles to use
Sans Serif

Colors

Designer to choose colors to be used in the design.

Requirements
Must have
• Posters need to be on and very stylish

```html
<!DOCTYPE html>
<html lang="en">
<head>
<meta charset="utf-8">
<title>Brookloft Quote Poster Set – Quit Talking</title>
<link rel="stylesheet" href="https://fonts.googleapis.com/css2?family=Poppins:wght@600;700&display=swap">
<style>
  :root {
    --poster-orange: #e8611e;
    --accent-red: rgba(214, 56, 30, 0.82);
    --ink-white: #ffffff;
  }
  html, body {
    margin: 0;
    padding: 0;
    width: 802px;
    height: 1200px;
    overflow: hidden;
    background: var(--poster-orange);
  }
  .poster {
    position: relative;
    width: 802px;
    height: 1200px;
    overflow: hidden;
    background: var(--poster-orange);
    font-family: "Poppins", Arial, sans-serif;
    color: var(--ink-white);
  }
  .quote-lead {
    position: absolute;
    left: 46px;
    top: 46px;
    margin: 0;
    font-size: 42px;
    font-weight: 700;
    line-height: 44px;
    letter-spacing: -0.5px;
  }
  .quote-main {
    margin: 0;
    font-size: 210px;
    font-weight: 700;
    line-height: 1;
    letter-spacing: -2px;
    white-space: nowrap;
  }
  .quote-line {
    position: absolute;
    left: 38px;
    display: block;
  }
  .quote-line--quit { top: 122px; }
  .quote-line--talking { top: 330px; }
  .quote-line--start { top: 530px; }
  .quote-line--doing { top: 726px; }
  .underline-bar {
    position: absolute;
    left: 48px;
    width: 652px;
    height: 19px;
    background: var(--accent-red);
    z-index: 2;
  }
  .underline-bar--start { top: 706px; }
  .underline-bar--doing { top: 901px; }
  .attribution {
    position: absolute;
    left: 46px;
    top: 1012px;
    margin: 0;
    font-size: 19px;
    font-weight: 600;
    line-height: 30px;
  }
  .brand-name {
    position: absolute;
    left: 46px;
    top: 1106px;
    margin: 0;
    display: flex;
    align-items: center;
    gap: 12px;
    font-size: 28px;
    font-weight: 600;
    line-height: 1;
    color: var(--ink-white);
  }
  .brand-dot {
    width: 14px;
    height: 14px;
    background: var(--ink-white);
  }
</style>
</head>
<body>
  <main class="poster">
    <p class="quote-lead">the way to get<br>started is to</p>
    <h1 class="quote-main">
      <span class="quote-line quote-line--quit">quit</span>
      <span class="quote-line quote-line--talking">talking</span>
      <span class="quote-line quote-line--start">start</span>
      <span class="quote-line quote-line--doing">doing</span>
    </h1>
    <div class="underline-bar underline-bar--start"></div>
    <div class="underline-bar underline-bar--doing"></div>
    <p class="attribution">Wendell Dunmore,<br>Co Founder, Dunmore Studios</p>
    <p class="brand-name"><span class="brand-dot"></span>Brookloft</p>
  </main>
</body>
</html>
```